Cozy Cradle Loops Needs a Beautiful Website

I need a new website for this new E-commerce. I sell handmade baby crochets, e.g. booties, headbands, hats, etc. I need a feminine and soft design to make the moms-to-be say 'oohh ahh'. I'd like pink, blue and gray. I'd like an inviting homepage, and nice regular pages where people can see and order the products.

Industry/Entity Type

Baby

Requirements
Must have
• beautiful, soft, feminine design. Please use pictures of the colors I'd like: brown, yellow, pink and blue. Any combination, but definitely include brown.

```html
<!DOCTYPE html>
<html lang="en">
<head>
<meta charset="utf-8">
<title>Cozy Cradle Loops</title>
<link href="https://fonts.googleapis.com/css2?family=PT+Sans:wght@400;700&family=PT+Serif:ital,wght@0,400;0,700;1,400;1,700&display=swap" rel="stylesheet">
<style>
:root{
  --sky:#0aa3cf;
  --sky-deep:#0796c2;
  --pink:#e8287d;
  --blue:#1aa7d3;
  --blue-text:#0b84b4;
  --ink:#222;
  --line:#dcdcdc;
  --panel:#f3f3f3;
  --white:#fff;
}
*{box-sizing:border-box;margin:0;padding:0}
html,body{width:1170px;height:1200px;overflow:hidden}
body{background:var(--sky);font-family:"PT Sans",Arial,sans-serif;color:var(--ink);position:relative}
.ground{position:absolute;left:0;bottom:0;width:1170px;height:70px}
.page{position:absolute;left:212px;top:0;width:748px;height:1060px;background:var(--white);overflow:hidden}
.abs{position:absolute}
.logo{left:28px;top:24px;font-family:"PT Serif",serif;font-weight:700;font-size:22px;color:var(--pink);display:flex;align-items:center;gap:6px}
.logo .dot{width:12px;height:12px;border-radius:50%;background:var(--blue)}
.cart{left:532px;top:20px;width:204px;height:25px;border:1px solid var(--line);box-shadow:0 1px 2px rgba(0,0,0,.15);font-size:8.5px;display:flex;align-items:center;padding:0 20px;justify-content:space-between}
.cart em{font-style:normal;color:var(--pink)}
.cart a{color:var(--blue-text);text-decoration:none}
.nav{left:12px;top:70px;width:724px;height:31px;background:var(--pink)}
.nav a{position:absolute;top:0;font-family:"PT Serif",serif;font-style:italic;font-weight:700;font-size:11.5px;color:var(--white);text-decoration:none;height:31px;line-height:31px}
.nav .home{left:0;background:var(--blue);width:61px;text-align:center}
.search{position:absolute;right:12px;top:6px;width:180px;height:20px;background:var(--white);border-radius:10px;border:1px solid #ddd;font-size:9px;color:#999;font-style:italic;line-height:18px;padding-left:10px}
.search b{position:absolute;right:1px;top:1px;height:16px;width:28px;border-radius:8px;background:#ddd;color:#333;font-style:normal;font-family:"PT Serif",serif;text-align:center;line-height:16px;font-size:9px}
.hero{left:13px;top:114px;width:722px;height:243px;border-radius:3px;overflow:hidden;background:linear-gradient(90deg,#8a8f3a 0%,#a48a3c 35%,#6f6a3a 55%,#8b6a3c 80%,#c98a2c 100%)}
.hero .photo{position:absolute;left:370px;top:0;width:352px;height:243px;background:linear-gradient(135deg,#b9708f 0%,#7c3c48 45%,#4c3c30 70%,#d28a2a 100%);opacity:.85}
.hero h1{position:absolute;left:32px;top:16px;font-family:"PT Serif",serif;font-style:italic;font-weight:700;font-size:48px;color:var(--pink);line-height:1.1}
.hero h2{position:absolute;left:32px;top:88px;font-family:"PT Serif",serif;font-weight:400;font-size:14.5px;color:var(--white)}
.hero p{position:absolute;left:32px;top:116px;width:310px;font-size:11px;line-height:17.6px;color:var(--white)}
.btn-shop{position:absolute;left:31px;top:187px;width:93px;height:28px;border-radius:3px;background:var(--blue);color:var(--white);font-family:"PT Serif",serif;font-style:italic;font-weight:700;font-size:13px;text-align:center;line-height:28px;box-shadow:0 1px 2px rgba(0,0,0,.3)}
.dots{position:absolute;left:683px;top:223px;display:flex;gap:5px}
.dots i{width:5px;height:5px;border-radius:50%;background:var(--white)}
.dots i:first-child{background:var(--pink)}
.side{left:13px;width:135px;background:linear-gradient(#fff,var(--panel));border:1px solid #e4e4e4;border-radius:3px;box-shadow:0 4px 4px -3px rgba(0,0,0,.15)}
.side h3{font-family:"PT Serif",serif;font-style:italic;font-weight:700;font-size:10.5px;color:#333;margin:10px 0 10px 10px}
.side li{list-style:none;font-size:9.2px;color:#333;height:17.6px}
.side li.more{color:var(--blue-text)}
.cat{top:370px;height:146px}.cat ul{padding-left:13px}
.price{top:528px;height:110px}.price ul{padding-left:20px}
.promo{left:13px;top:650px;width:135px;height:167px;border-radius:3px;overflow:hidden}
.promo .photo{height:130px;background:linear-gradient(160deg,#c9d8e6,#e9dcd2 55%,#f4f1ee)}
.promo .band{height:37px;background:var(--pink);color:var(--white);font-family:"PT Serif",serif;font-weight:700;font-size:12.5px;line-height:37px;text-align:center}
.sec-head{left:158px;width:578px;height:26px;background:linear-gradient(var(--blue),var(--sky-deep));border-radius:2px 2px 0 0;color:var(--white);font-family:"PT Serif",serif;font-weight:700;font-size:11.5px;line-height:26px;padding-left:10px;border-bottom:2px solid #9bd7ea}
.grid{left:158px;width:578px;display:flex;gap:11px}
.card{width:136px;height:172px;border:1px solid var(--line);position:relative;flex:none}
.card h4{font-weight:400;font-size:9.5px;color:var(--blue-text);position:absolute;left:9px;top:6px}
.card .shot{position:absolute;left:7px;top:21px;width:121px;height:120px}
.card .cost{position:absolute;left:6px;top:152px;font-weight:700;font-size:11.5px}
.card .buy{position:absolute;right:6px;top:148px;width:64px;height:18px;border-radius:4px;background:var(--pink);color:var(--white);font-family:"PT Serif",serif;font-style:italic;font-weight:700;font-size:9.5px;text-align:center;line-height:18px;box-shadow:0 1px 2px rgba(0,0,0,.3)}
.welcome-title{left:162px;top:840px;font-family:"PT Serif",serif;font-weight:700;font-size:12.5px;color:var(--blue-text)}
.welcome-img{left:162px;top:872px;width:149px;height:106px;background:linear-gradient(135deg,#8a3a3a,#5a6070 40%,#c9b45a 70%,#3d4a3e)}
.welcome-text{left:322px;top:868px;width:404px;font-size:9.2px;line-height:16px;text-align:justify;color:#222}
.footer{left:12px;top:1016px;width:724px;height:29px;background:var(--pink)}
.footer a{position:absolute;top:0;line-height:29px;font-family:"PT Serif",serif;font-style:italic;font-weight:700;font-size:9.6px;color:var(--white);text-decoration:none}
.footer .sep{position:absolute;top:0;line-height:29px;color:var(--white);font-size:8px}
.social{position:absolute;right:52px;top:10px;display:flex;gap:8px}
.social i{width:10px;height:10px;border-radius:50%;background:var(--white)}
</style>
</head>
<body>
<svg class="ground" viewBox="0 0 1170 70" preserveAspectRatio="none" aria-hidden="true">
  <path d="M0 22 C200 40 360 60 600 52 C820 44 980 28 1170 24 L1170 70 L0 70 Z" fill="#fff"/>
</svg>

<div class="page">
  <div class="abs logo"><span>Cozy Cradle Loops</span><span class="dot"></span></div>
  <div class="abs cart"><span>Shopping Cart: <em>0 items</em></span><a href="#">View cart</a></div>

  <nav class="abs nav">
    <a class="home" href="#">Home</a>
    <a href="#" style="left:78px">About Us</a>
    <a href="#" style="left:161px">New Arrials</a>
    <a href="#" style="left:270px">Baby Crochets</a>
    <a href="#" style="left:383px">Blog</a>
    <a href="#" style="left:438px">Contact</a>
    <div class="search">Search<b>GO</b></div>
  </nav>

  <section class="abs hero">
    <div class="photo" role="img" aria-label="Toddler in a pink knitted hat and striped scarf holding autumn leaves"></div>
    <h1>New Arrials</h1>
    <h2>DOLOR SIT AMET, CONSECTETUR ADIPISCING ELIT.</h2>
    <p>Ut metus felis, posuere ac eleifend eget, tristique id magna.<br>In iaculis pellentesque nisl vel blandit. Phasellus ac orci eget<br>mi malesuada varius ac quis purus.</p>
    <div class="btn-shop">Shop Now</div>
    <div class="dots"><i></i><i></i><i></i><i></i></div>
  </section>

  <aside class="abs side cat">
    <h3>Shop by Category</h3>
    <ul><li>Crochets</li><li>Booties</li><li>Headbands,</li><li>Hats</li><li class="more">More</li></ul>
  </aside>
  <aside class="abs side price">
    <h3>Shop by Price</h3>
    <ul><li>Under $25</li><li>$25 - $50</li><li>$50 - $100</li><li>Over $100</li></ul>
  </aside>
  <div class="abs promo">
    <div class="photo" role="img" aria-label="Sleeping newborn in a blue knitted hat"></div>
    <div class="band">Exclusive Discount</div>
  </div>

  <div class="abs sec-head" style="top:370px">FEATURED PRODUCTS</div>
  <div class="abs grid" style="top:406px">
    <div class="card"><h4>Product #001</h4><div class="shot" role="img" aria-label="Pink crochet crown headband" style="background:linear-gradient(#f4f4f4,#f7b3cf 50%,#f4f4f4)"></div><span class="cost">$78.88</span><span class="buy">Buy Now</span></div>
    <div class="card"><h4>Product #002</h4><div class="shot" role="img" aria-label="Pale pink crochet booties with roses" style="background:linear-gradient(#e9c3cf,#f1dfe2 50%,#d9d5cf)"></div><span class="cost">$18.88</span><span class="buy">Buy Now</span></div>
    <div class="card"><h4>Product #003</h4><div class="shot" role="img" aria-label="Teal crochet booties" style="background:linear-gradient(#3a8f9c,#2f8f99 50%,#6a7f88)"></div><span class="cost">$24.88</span><span class="buy">Buy Now</span></div>
    <div class="card"><h4>Product #004</h4><div class="shot" role="img" aria-label="Aqua crochet crown headband" style="background:linear-gradient(#f4f4f4,#8fdbe6 50%,#f0f0f0)"></div><span class="cost">$111.00</span><span class="buy">Buy Now</span></div>
  </div>

  <div class="abs sec-head" style="top:610px">OUR PRODUCTS</div>
  <div class="abs grid" style="top:646px">
    <div class="card"><h4>Product #005</h4><div class="shot" role="img" aria-label="Gray crochet booties with red rose" style="background:linear-gradient(#6a6a6a,#5a5a5a 60%,#8a8a8a)"></div><span class="cost">$78.88</span><span class="buy">Buy Now</span></div>
    <div class="card"><h4>Product #006</h4><div class="shot" role="img" aria-label="Red crochet booties" style="background:linear-gradient(#7a7a7a,#b52424 50%,#8a7a7a)"></div><span class="cost">$36.88</span><span class="buy">Buy Now</span></div>
    <div class="card"><h4>Product #003</h4><div class="shot" role="img" aria-label="Pink crochet crown headband" style="background:linear-gradient(#f2f2f2,#ea8fd6 50%,#f2f2f2)"></div><span class="cost">$85.00</span><span class="buy">Buy Now</span></div>
    <div class="card"><h4>Product #003</h4><div class="shot" role="img" aria-label="Brown crochet sneaker booties" style="background:linear-gradient(#6a3a5a,#5a4238 50%,#e4dcd6)"></div><span class="cost">$14.88</span><span class="buy">Buy Now</span></div>
  </div>

  <h2 class="abs welcome-title">WELCOME TO COZY CRADLE LOOPS</h2>
  <div class="abs welcome-img" role="img" aria-label="Collage of colourful crochet sneaker booties"></div>
  <p class="abs welcome-text">Consectetur adipisicing elit, sed do eiusmod tempor incididunt ut labore et dolore magna aliqua. Ut enim ad minim veniam, quis nostrud exercitation ullamco laboris nisi ut aliquip ex ea commodo consequat. Duis aute irure dolor in reprehenderit in voluptate velit esse cillum dolore eu fugiat nulla pariatur. Excepteur sint occaecat cupidatat non proident, sunt in culpa qui officia deserunt mollit anim id est laborum.Consectetur adipisicing elit, sed do eiusmod tempor incididunt ut labore et dolore magna aliqua. Ut enim ad minim veniam, quis nostrud exercitation ullamco laboris nisi ut aliquip ex ea commodo consequat. Duis aute irure dolor in reprehenderit in voluptate velit</p>

  <footer class="abs footer">
    <a href="#" style="left:23px">Home</a><span class="sep" style="left:58px">I</span>
    <a href="#" style="left:67px">About Us</a><span class="sep" style="left:118px">I</span>
    <a href="#" style="left:125px">New Arrials</a><span class="sep" style="left:192px">I</span>
    <a href="#" style="left:203px">Baby Crochets</a><span class="sep" style="left:282px">I</span>
    <a href="#" style="left:292px">Blog</a><span class="sep" style="left:322px">I</span>
    <a href="#" style="left:331px">Contact</a>
    <div class="social"><i></i><i></i><i></i><i></i></div>
  </footer>
</div>
</body>
</html>
```